Clean & Inspiring Web Design Project

Tallowmere Object Works, LLC (also known as T7-Works) is a company which provides 3D printing services and products. The emphasis is on making these products and services available to the mass-market - customers and users who may or may not have prior experience with 3D printing and/or rapid prototyping technologies. We are a start-up company, looking to build a clean and creativity inspiring brand - our site must encourage visitor to engage and make something. Our aim is to help take mere ideas and turn them into tangible items. We want to show a fusion of ideas (e.g. pencil sketches on graph paper) with design tools (e.g. CAD and drafting software) and rapid prototyping (e.g. Kindlo 3D printers, Stereolithography Machines, etc.). We would like the website to appear professional but at the same time easy to navigate and a good balance between text and pictures. The final design should inspire customers to nurture their ideas into real products and communicate our services to our customers. Our site should have the feel of a vibrant social community with the added benefit of tangible physical creations.

Target Market(s)

People with great ideas that need to be designed into a real product

Industry/Entity Type

Printing

Requirements
Must have
• - Website design should include 2 layouts - one for a "landing page" and one for a "content page"
- Website design must incorporate attached company logo (or derivative of this logo)
- Website design should incorporate the menu options shown in the attached PDF UI concept (UI does not necessarily need to look like the provided concept, just include all the clickable elements)
- Website design must portray an innovative and cooperative design environment with a look-and-feel that appeals to both amateur and professional designers.
- Please include pictures, illustrations and photographs (as needed) related to 3D printing, CAD design, conventional drafting, engineering and manufacturing industries.
- Design should support scaling to multiple screen sizes, from tablet computers (e.g. Zelo) to very large screen PCs.
- Design should include Username & Password fields for login or a button to pull up a login popup.
Nice to have
• - Website design could include "Invent", "Make", "Produce" and "Buy" options that slowly cycle through - with appropriate photos / graphics. These "menu options" would also be mouse-over enabled to switch into the appropriate context as the cursor enters that region (e.g. mouse over the "Invent" text would bring up page 2, etc.). (See attached Original UI Thoughts)
Should not have
• Requirements - Should Not Have:
- Website design should not portray a service that is very expensive or complicated - we are a reasonably priced service meant to be friendly with amateur inventors
- Website design should not be overly complicated - please keep it reasonably simple
- Website design should not be overly trendy
- Website design should not use more than 2 font styles, gaudy fonts, etc.
- Website design should not be "campy" or "tacky" - playful is ok, but please keep it elegant
- Website design should not be overly masculine or feminine - we will have both women and men as customers

```html
<!DOCTYPE html>
<html lang="en">
<head>
<meta charset="utf-8">
<title>T7-Works — 3D Printing Services</title>
<link href="https://fonts.googleapis.com/css2?family=Open+Sans:wght@400;600;700&family=Source+Sans+3:wght@400;600;700&display=swap" rel="stylesheet">
<style>
  :root{
    --brand-blue:#03669c;
    --nav-blue:#0b5f95;
    --tab-blue:#4b9bd3;
    --hero-glow:#16aee0;
    --band-grey:#f2f2f2;
    --card-white:#ffffff;
    --text-dark:#111111;
    --text-grey:#666666;
    --text-soft:#8a8a8a;
    --icon-grey:#8f8f8f;
    --photo-store:#6d6a68;
    --photo-printer:#3b3f44;
    --photo-part:#e9e7e1;
  }
  *{margin:0;padding:0;box-sizing:border-box}
  html,body{width:1200px;height:1176px;overflow:hidden;background:#fff}
  body{position:relative;font-family:"Source Sans 3",sans-serif;color:var(--text-dark)}
  a{color:inherit;text-decoration:none}

  .top-bar{position:absolute;left:0;top:0;width:1200px;height:53px;background:var(--brand-blue)}
  .shop-pill{position:absolute;left:890px;top:16px;width:59px;height:23px;border-radius:12px 0 0 12px;background:#e6e6e6;color:#333;font-weight:700;font-size:14px;line-height:23px;text-align:center}
  .cart{position:absolute;left:961px;top:15px;display:flex;align-items:center;gap:12px;color:#fff;font-size:14px}
  .cart b{font-weight:700}

  .main-nav{position:absolute;left:0;top:53px;width:1200px;height:86px;background:var(--band-grey)}
  .brand{position:absolute;left:118px;top:14px;display:flex;align-items:center;gap:12px}
  .brand-mark{width:56px;height:56px;background:var(--brand-blue);border-radius:6px}
  .brand-name{font-family:"Open Sans",sans-serif;font-weight:700;font-size:26px;color:#555}
  .nav-links{position:absolute;top:32px;left:0;font-size:21px;color:var(--nav-blue)}
  .nav-links a{position:absolute;white-space:nowrap}

  .hero{position:absolute;left:0;top:139px;width:1200px;height:504px;
    background:radial-gradient(ellipse 700px 300px at 20% 58%,var(--hero-glow) 0%,#0a86c0 45%,var(--brand-blue) 80%)}
  .hero::after{content:"";position:absolute;left:0;top:315px;width:100%;height:189px;background:linear-gradient(180deg,rgba(0,60,110,.12),rgba(0,60,110,.2))}
  .sub-nav{position:absolute;left:258px;top:30px;width:684px;height:60px;background:var(--tab-blue);border-radius:10px}
  .sub-nav .label{position:absolute;left:78px;top:14px;font-family:"Open Sans",sans-serif;font-weight:700;font-size:21px;color:#fff}
  .sub-nav .tab{position:absolute;top:14px;height:29px;line-height:29px;font-size:14px;color:#fff;text-transform:uppercase}
  .sub-nav .tab.active{background:var(--brand-blue);border-radius:15px;width:112px;text-align:center}
  .feature-card{position:absolute;z-index:2;left:94px;top:82px;width:1012px;height:360px;background:var(--card-white);border-radius:11px;box-shadow:0 14px 28px rgba(0,40,80,.35)}
  .feature-title{position:absolute;left:38px;top:66px;font-family:"Open Sans",sans-serif;font-size:47px;color:#555;font-weight:400;letter-spacing:-.5px;white-space:nowrap}
  .feature-title b{font-weight:700}
  .feature-text{position:absolute;left:39px;top:130px;width:470px;font-size:14px;line-height:27px;color:var(--text-grey)}
  .feature-photo{position:absolute;left:565px;top:32px;width:406px;height:294px;border-radius:40px;
    background:radial-gradient(ellipse at 50% 50%,var(--photo-part) 0%,#f4f3ef 55%,#fff 80%)}

  .column{position:absolute;top:667px;width:290px}
  .col-store{left:108px}.col-printers{left:450px}.col-blog{left:792px}
  .column-head{height:43px;border-radius:10px;background:var(--brand-blue);color:#fff;text-align:center;font-family:"Open Sans",sans-serif;font-weight:600;font-size:25px;line-height:43px;box-shadow:0 10px 12px -6px rgba(0,0,0,.25)}
  .column-photo{position:absolute;width:267px;height:111px}
  .col-store .column-photo{left:7px;top:54px;background:linear-gradient(135deg,#8a8582,var(--photo-store) 60%,#4c4a49)}
  .col-printers .column-photo{left:12px;top:50px;background:linear-gradient(160deg,#5b6168,var(--photo-printer) 55%,#23262a)}
  .column-text{position:absolute;left:5px;width:292px;font-size:13px;line-height:18.8px}
  .col-store .column-text{top:172px}
  .col-printers .column-text{left:13px;top:167px;width:292px}
  .read-more{position:absolute;top:343px;left:7px;font-size:13px}
  .col-printers .read-more{left:13px}
  .col-blog .read-more{left:4px}

  .blog-item{position:absolute;left:2px;display:flex;gap:13px;width:290px}
  .blog-icon{flex:none;width:43px;height:49px;background:var(--brand-blue);border-radius:5px}
  .blog-title{font-size:13px;line-height:19px}
  .blog-meta{font-size:9.5px;color:var(--text-soft);font-weight:600;letter-spacing:.6px;margin-top:1px}
  .blog-rule{position:absolute;left:23px;width:254px;border-top:1px dotted #777}

  .social{position:absolute;left:124px;top:1076px;display:flex;gap:14px;align-items:center}
  .social-dot{width:35px;height:35px;border-radius:50%;background:var(--icon-grey)}
  .social-dot.primary{background:var(--brand-blue)}
  .footer-links{position:absolute;left:112px;top:1129px;font-size:14px;color:#555}
  .footer-brand{position:absolute;left:809px;top:1064px;display:flex;align-items:center;gap:12px}
  .footer-mark{flex:none;width:38px;height:44px;background:var(--brand-blue);border-radius:5px}
  .footer-name{font-size:22px;font-weight:700;line-height:26px;color:var(--text-dark)}
</style>
</head>
<body>
  <header class="top-bar">
    <a class="shop-pill" href="#">SHOP</a>
    <a class="cart" href="#">
      <svg width="24" height="22" viewBox="0 0 24 22" aria-hidden="true"><path d="M1 3h4l3 11h12l3-8H7" fill="none" stroke="#fff" stroke-width="1.8" stroke-linejoin="round"/><circle cx="10" cy="18" r="2" fill="#fff"/><circle cx="18" cy="18" r="2" fill="#fff"/></svg>
      <span>Cart <b>(0)</b></span>
    </a>
  </header>

  <nav class="main-nav">
    <a class="brand" href="#"><span class="brand-mark"></span><span class="brand-name">T7-Works</span></a>
    <div class="nav-links">
      <a href="#" style="left:406px">WHY T7</a>
      <a href="#" style="left:560px">DREAMER</a>
      <a href="#" style="left:733px">MAKER</a>
      <a href="#" style="left:868px">PRODUCER</a>
    </div>
  </nav>

  <section class="hero">
    <div class="sub-nav">
      <span class="label">ABOUT T7</span>
      <a class="tab active" href="#" style="left:260px">Dream</a>
      <a class="tab" href="#" style="left:396px">Make</a>
      <a class="tab" href="#" style="left:471px">Produce</a>
      <a class="tab" href="#" style="left:578px">Sell</a>
    </div>
    <div class="feature-card">
      <h1 class="feature-title"><b>3D</b> Printing <b>Services</b></h1>
      <p class="feature-text">Lorem Ipsum is simply dummy text of the printing and typesetting industry. Lorem Ipsum has been the industry's standard dummy text ever since the 1500s, when an unknown printer took a galley of type and scrambled it to make a type specimen book. It has survived not only five centuries, but also the leap into electronic typesetting, remaining essentially unchanged.</p>
      <div class="feature-photo" role="img" aria-label="Photo of a white 3D printed cylindrical part with ribbed and perforated sections"></div>
    </div>
  </section>

  <section class="column col-store">
    <h2 class="column-head">T7 STORE</h2>
    <div class="column-photo" role="img" aria-label="Photo of a store wall displaying colourful 3D printing filament spools"></div>
    <p class="column-text">Lorem Ipsum is simply dummy text of the printing and typesetting industry. Lorem Ipsum has been the industry's standard dummy text ever since the 1500s, when an unknown printer took a galley of type and scrambled it to make a type specimen book. It has survived not only five centuries, but also the leap into electronic typesetting, remaining essentially unchanged.</p>
    <a class="read-more" href="#">Read more &gt;&gt;</a>
  </section>

  <section class="column col-printers">
    <h2 class="column-head">T7 PRINTERS</h2>
    <div class="column-photo" role="img" aria-label="Photo of the inside of a 3D printer building a white part"></div>
    <p class="column-text">Lorem Ipsum is simply dummy text of the printing and typesetting industry. Lorem Ipsum has been the industry's standard dummy text ever since the 1500s, when an unknown printer took a galley of type and scrambled it to make a type specimen book. It has survived not only five centuries, but also the leap into electronic typesetting, remaining essentially unchanged.</p>
    <a class="read-more" href="#">Read more &gt;&gt;</a>
  </section>

  <section class="column col-blog">
    <h2 class="column-head">T7 BLOG</h2>
    <article class="blog-item" style="top:68px"><span class="blog-icon"></span><div><p class="blog-title">Lorem Ipsum is simply dummy text of the printing and typesetting industry.</p><p class="blog-meta">Oct 13 ,2012 Fews Days Ago ,Time: 1.00 PM</p></div></article>
    <div class="blog-rule" style="top:140px"></div>
    <article class="blog-item" style="top:164px"><span class="blog-icon"></span><div><p class="blog-title">Lorem Ipsum is simply dummy text of the printing and typesetting industry.</p><p class="blog-meta">Oct 13 ,2012 Fews Days Ago ,Time: 1.00 PM</p></div></article>
    <div class="blog-rule" style="top:236px"></div>
    <article class="blog-item" style="top:262px"><span class="blog-icon"></span><div><p class="blog-title">Lorem Ipsum is simply dummy text of the printing and typesetting industry.</p><p class="blog-meta">Oct 13 ,2012 Fews Days Ago ,Time: 1.00 PM</p></div></article>
    <a class="read-more" href="#">Read more &gt;&gt;</a>
  </section>

  <footer>
    <div class="social">
      <a class="social-dot primary" href="#" aria-label="Social profile"></a>
      <a class="social-dot" href="#" aria-label="Social profile"></a>
      <a class="social-dot" href="#" aria-label="Video channel"></a>
      <a class="social-dot" href="#" aria-label="Social profile"></a>
      <a href="#" aria-label="Email">
        <svg width="40" height="34" viewBox="0 0 40 34" aria-hidden="true"><g transform="rotate(-12 20 17)"><rect x="3" y="7" width="34" height="21" rx="2" fill="var(--icon-grey)"/><path d="M4 8l16 12L36 8" fill="none" stroke="#fff" stroke-width="2"/></g></svg>
      </a>
    </div>
    <p class="footer-links"><a href="#">Home</a> | <a href="#">Contact</a> | <a href="#">Franchise</a> | &nbsp;<a href="#">Distributors</a> | <a href="#">Cart</a></p>
    <div class="footer-brand">
      <span class="footer-mark"></span>
      <p class="footer-name">Tallowmere<br>Object Works</p>
    </div>
  </footer>
</body>
</html>
```